Mira Bloom Fitness Coaching Project

I am a personal trainer based in London. My services include one-on-one PT sessions, bootcamps.
I would like the design to be minimalistic. With light colours: white, pink, purple.
I specialise in weight loss, flexibility, mobility.

Tessa Brogan
Personal Trainer
Email: tessa.brogan@quellmail.com
tel: 07700218493
Instagram: Mira Bloom

Target Market(s)

adults, mostly females (age 18-50).

Industry/Entity Type

Fitness

Contact Information for Business Card

Tessa Brogan
Personal Trainer
tel: 07700218493
Instagram: Mira Bloom

Font styles to use
Serif

Colors
eea4c8
fbd4d5
fdf9cf
cfeae6
cee9f5

Requirements
Nice to have
• minimalistic style
• easy to read and remember

```html
<!DOCTYPE html>
<html lang="en">
<head>
<meta charset="utf-8">
<title>Tessa Brogan – Business Card</title>
<link rel="stylesheet" href="https://fonts.googleapis.com/css2?family=Lora:wght@400;500;600&display=swap">
<style>
  :root {
    --page-bg: #fdf6f6;
    --card-bg: #fffdfb;
    --card-edge: #f3d3dc;
    --blush: #fbd4d5;
    --rose: #eea4c8;
    --rose-deep: #d27fab;
    --ink: #6a2e6e;
    --ink-soft: #86568a;
    --photo-warm: #e8b9b0;
    --photo-mid: #f2cfd0;
    --photo-light: #fdf9cf;
  }
  * { margin: 0; padding: 0; box-sizing: border-box; }
  html, body {
    width: 1200px;
    height: 969px;
    overflow: hidden;
    background: var(--page-bg);
    font-family: "Lora", serif;
  }
  .business-card {
    position: absolute;
    left: 356px;
    top: 54px;
    width: 488px;
    height: 860px;
    border-radius: 26px;
    background: var(--card-bg);
    border: 1px solid var(--card-edge);
    overflow: hidden;
  }
  .portrait-header {
    position: absolute;
    left: 0;
    top: 0;
    width: 488px;
    height: 420px;
  }
  .card-body {
    position: absolute;
    left: 58px;
    top: 460px;
    right: 36px;
    color: var(--ink);
  }
  .trainer-name {
    font-weight: 600;
    font-size: 42px;
    letter-spacing: 1px;
    line-height: 1.05;
    text-transform: uppercase;
    white-space: nowrap;
  }
  .trainer-role {
    margin-top: 10px;
    font-weight: 400;
    font-size: 19px;
    letter-spacing: 0.5px;
    color: var(--ink-soft);
    text-transform: uppercase;
  }
  .contact-list {
    list-style: none;
    margin-top: 46px;
  }
  .contact-item {
    display: flex;
    align-items: center;
    gap: 14px;
    height: 28px;
    font-weight: 400;
    font-size: 17px;
    color: var(--ink-soft);
    text-transform: uppercase;
    white-space: nowrap;
  }
  .contact-icon {
    width: 18px;
    height: 18px;
    flex: none;
  }
  .social-square {
    width: 15px;
    height: 15px;
    margin: 0 1px 0 2px;
    background: var(--rose);
    border-radius: 3px;
    flex: none;
  }
  .services-title {
    margin-top: 42px;
    font-weight: 600;
    font-size: 24px;
    letter-spacing: 0.5px;
    text-transform: uppercase;
    color: var(--ink);
  }
  .service-list {
    list-style: none;
    margin-top: 8px;
  }
  .service-item {
    display: flex;
    align-items: center;
    gap: 10px;
    height: 28px;
    font-weight: 400;
    font-size: 17px;
    color: var(--ink-soft);
    text-transform: uppercase;
  }
  .service-item::before {
    content: "";
    width: 8px;
    height: 8px;
    border-radius: 50%;
    background: var(--rose-deep);
    flex: none;
  }
</style>
</head>
<body>
  <div class="business-card">
    <svg class="portrait-header" viewBox="0 0 488 420">
      <defs>
        <radialGradient id="portraitTone" cx="0.45" cy="0.35" r="0.8">
          <stop offset="0" stop-color="#fdf9cf"/>
          <stop offset="0.5" stop-color="#f2cfd0"/>
          <stop offset="1" stop-color="#e8b9b0"/>
        </radialGradient>
      </defs>
      <path role="img" aria-label="Portrait photo of the trainer, smiling, with long curly hair in warm sunlight"
            d="M0,0 H488 V380 C420,405 340,385 260,360 C180,335 90,325 0,345 Z"
            fill="url(#portraitTone)"/>
      <path class="wave-band"
            d="M0,345 C90,325 180,335 260,360 C340,385 420,405 488,380 V398 C420,420 340,402 260,378 C180,354 90,344 0,362 Z"
            fill="#eea4c8"/>
      <path class="wave-line"
            d="M0,362 C90,344 180,354 260,378 C340,402 420,420 488,398"
            fill="none" stroke="#6a2e6e" stroke-width="2"/>
    </svg>

    <div class="card-body">
      <h1 class="trainer-name">Tessa Brogan</h1>
      <p class="trainer-role">Personal Trainer</p>

      <ul class="contact-list">
        <li class="contact-item">
          <svg class="contact-icon" viewBox="0 0 24 24" aria-hidden="true">
            <path d="M6.6 10.8a15.2 15.2 0 0 0 6.6 6.6l2.2-2.2a1 1 0 0 1 1-.25 11.4 11.4 0 0 0 3.6.57 1 1 0 0 1 1 1V20a1 1 0 0 1-1 1A17 17 0 0 1 3 4a1 1 0 0 1 1-1h3.5a1 1 0 0 1 1 1c0 1.25.2 2.45.57 3.57a1 1 0 0 1-.25 1z" fill="#eea4c8"/>
          </svg>
          <span>07700218493</span>
        </li>
        <li class="contact-item">
          <svg class="contact-icon" viewBox="0 0 24 24" aria-hidden="true">
            <rect x="2" y="5" width="20" height="14" rx="1.5" fill="#eea4c8"/>
            <path d="M3 6.5l9 6.5 9-6.5" fill="none" stroke="#fffdfb" stroke-width="1.6"/>
          </svg>
          <span>tessa.brogan@quellmail.com</span>
        </li>
        <li class="contact-item">
          <span class="social-square" aria-hidden="true"></span>
          <span>Mira Bloom</span>
        </li>
      </ul>

      <h2 class="services-title">Service</h2>
      <ul class="service-list">
        <li class="service-item">PT Sessions</li>
        <li class="service-item">Bootcamps.</li>
      </ul>
    </div>
  </div>
</body>
</html>
```